Chimney Service company needs new business card design

We need a updated business card with our new logo added. We provide a full range of chimney services throughout Vermont and New Hampshire. The business card will be one sided and color. Attached is our current business card another document showing all the information we would like on the card.
We dont like a lot of flashy colors.... here is a link to our website to get an idea of our branding www.flueguardianvt.example

Target Market(s)

homeowners

Industry/Entity Type

Business

Contact Information for Business Card

See attached sheet for content.

Font styles to use
Serif
Sans Serif

Requirements
Must have
• all information provided on separate sheet
Should not have
• Additional information that may clogg up design

```html
<!DOCTYPE html>
<html lang="en">
<head>
<meta charset="utf-8">
<title>Flue Guardian – Business Card</title>
<link rel="stylesheet" href="https://fonts.googleapis.com/css2?family=Open+Sans:wdth,wght@75..100,400;75..100,600;75..100,700&display=swap">
<style>
  :root {
    --backdrop: #b9b9b9;
    --charcoal: #333333;
    --ink: #2b2b2b;
    --band-grey: #5a5a5a;
    --card-white: #f2f2f2;
    --brand-red: #8e0f12;
    --accent-red: #b3161b;
    --text-white: #ffffff;
  }
  * { box-sizing: border-box; margin: 0; padding: 0; }
  html, body { width: 1200px; height: 576px; overflow: hidden; }
  body {
    background: var(--backdrop);
    font-family: "Open Sans", Arial, sans-serif;
    position: relative;
  }
  .card {
    position: absolute;
    border-radius: 14px;
    overflow: hidden;
  }
  /* Front */
  .card-front {
    left: 82px; top: 138px; width: 484px; height: 294px;
    background: var(--charcoal);
  }
  .front-mark {
    position: absolute; left: 50%; top: 76px; transform: translateX(-50%);
    width: 104px; height: 104px; border: 9px solid var(--text-white);
  }
  .front-name {
    position: absolute; left: 0; right: 0; top: 186px;
    text-align: center; color: var(--text-white);
    font-weight: 600; font-size: 25px; letter-spacing: 1.5px;
  }
  /* Back */
  .card-back {
    left: 602px; top: 138px; width: 481px; height: 291px;
    background: linear-gradient(180deg, #f7f7f7, #e9e9e9);
  }
  .card-wave { position: absolute; left: 0; top: 0; width: 481px; height: 291px; }
  .service-list {
    position: absolute; left: 22px; top: 24px; list-style: none;
    font-size: 12.5px; color: var(--ink); line-height: 16.8px;
  }
  .service-list li { display: flex; align-items: center; gap: 8px; }
  .service-list li::before {
    content: ""; width: 6px; height: 6px; border-radius: 50%;
    background: var(--accent-red); flex: none;
  }
  .back-mark {
    position: absolute; left: 322px; top: 26px; width: 92px; height: 92px;
    border: 8px solid var(--ink);
  }
  .back-name {
    position: absolute; left: 288px; width: 180px; top: 128px; text-align: center;
    font-weight: 600; font-size: 16px; letter-spacing: 1px; color: var(--ink);
  }
  .service-area {
    position: absolute; left: 20px; top: 130px;
    font-weight: 700; font-stretch: 80%; font-size: 17px; color: var(--brand-red);
  }
  .since {
    position: absolute; left: 20px; top: 154px; width: 247px;
    display: flex; align-items: center; gap: 6px;
    font-size: 10.5px; color: var(--ink);
  }
  .since::before, .since::after { content: ""; flex: 1; height: 1.5px; background: var(--brand-red); }
  .contact-list {
    position: absolute; left: 22px; top: 176px; list-style: none;
    font-size: 12.5px; color: var(--ink); line-height: 19.5px;
  }
  .contact-list li { display: flex; align-items: center; gap: 8px; }
  .contact-list svg { width: 11px; height: 11px; fill: var(--accent-red); flex: none; }
  .web-accent { color: var(--accent-red); }
  .promise-list {
    position: absolute; right: 18px; top: 228px; list-style: none; text-align: right;
    font-size: 11.5px; color: var(--text-white); line-height: 15.3px;
  }
</style>
</head>
<body>
  <section class="card card-front">
    <div class="front-mark"></div>
    <p class="front-name">FLUE GUARDIAN</p>
  </section>

  <section class="card card-back">
    <svg class="card-wave" viewBox="0 0 481 291" aria-hidden="true">
      <path d="M0,262 C120,300 220,272 300,226 S430,182 481,184 L481,291 L0,291 Z" fill="var(--brand-red)"/>
      <path d="M30,262 C150,296 250,258 330,212 S445,168 481,166" fill="none" stroke="var(--ink)" stroke-width="8"/>
      <path d="M38,250 C150,280 245,246 325,202 S445,158 481,156" fill="none" stroke="var(--band-grey)" stroke-width="2.5"/>
    </svg>

    <ul class="service-list">
      <li>Full Masonry Services</li>
      <li>Historic chimney restoration</li>
      <li>Stainless steel liners</li>
      <li>New Chimney installations</li>
      <li>Guild Certified Chimney sweeps</li>
    </ul>

    <div class="back-mark"></div>
    <p class="back-name">FLUE GUARDIAN</p>

    <h2 class="service-area">Serving VT and New Hampshire</h2>
    <p class="since">SINCE 1989</p>

    <ul class="contact-list">
      <li><svg viewBox="0 0 12 12"><path d="M1,4 Q6,0 11,4 L9,5 L8,4 L4,4 L3,5 Z M3,6 L9,6 L10,11 L2,11 Z"/></svg>802-555-0147</li>
      <li><svg viewBox="0 0 12 12"><path d="M0,2 H12 V10 H0 Z" /><path d="M0,2 L6,7 L12,2" fill="none" stroke="#f2f2f2" stroke-width="1.2"/></svg>info@flueguardianvt.example</li>
      <li><svg viewBox="0 0 12 12"><circle cx="6" cy="6" r="5.5"/><path d="M0.5,6 H11.5 M6,0.5 V11.5 M6,0.5 Q2,6 6,11.5 M6,0.5 Q10,6 6,11.5" fill="none" stroke="#f2f2f2" stroke-width="0.9"/></svg><span>www.<span class="web-accent">flueguardianvt</span>.example</span></li>
    </ul>

    <ul class="promise-list">
      <li>Fully Insured &nbsp;«</li>
      <li>Free Estimates &nbsp;«</li>
      <li>Family Owned &amp; Operated &nbsp;«</li>
    </ul>
  </section>
</body>
</html>
```